Velvet Dice Night Age Verification Landing Page

To create a visually appealing design for the landing page of the adult game "Velvet Dice Night" that confirms the visitor's age.
The design should have a simple and visually appealing look that focuses on two buttons labeled "Yes" and "No". The purpose of the page is to confirm that the visitor is 18 years of age or older before accessing the game's content. Responsive design that works well on desktop and mobile devices. The final output should be delivered in PSD, AI, or Sketch format, along with any necessary images or assets.
I have also attached examples.

```html
<!DOCTYPE html>
<html lang="en">
<head>
<meta charset="utf-8">
<title>Velvet Dice Night – Age Check</title>
<link href="https://fonts.googleapis.com/css2?family=Inter:wght@400;500;600&family=Lexend:wght@400;500;600;700&display=swap" rel="stylesheet">
<style>
:root{
  --page-bg:#0b0a14;
  --band:#16143a;
  --ink:#e9e6f5;
  --muted:#9a97b0;
  --accent:#3b2bd6;
  --orange:#f29a1a;
  --line:#3a3850;
  --veil:rgba(0,0,0,.8);
  --modal:#9663a0;
  --modal-edge:#6b1f7d;
  --btn:#7b2d8e;
  --modal-ink:#1d0f21;
}
*{margin:0;padding:0;box-sizing:border-box}
html,body{width:1200px;height:1059px;overflow:hidden;background:var(--page-bg)}
body{position:relative;font-family:"Lexend",sans-serif;color:var(--ink)}
.abs{position:absolute}
.top-band{left:0;top:0;width:794px;height:99px;background:linear-gradient(90deg,#120f30,var(--band))}
.promo-title{left:946px;top:-14px;font-size:28px;font-weight:600;white-space:nowrap}
.btn{display:flex;align-items:center;justify-content:center;font-size:9px;letter-spacing:1.2px;font-weight:600;border-radius:8px;white-space:nowrap}
.btn-solid{background:var(--accent);color:#fff}
.btn-ghost{border:1.5px solid var(--line);color:var(--ink)}
.brand{left:30px;top:122px;display:flex;align-items:center;gap:10px;font-size:18px;font-weight:500}
.brand-mark{width:22px;height:22px;border:2px solid var(--ink);border-radius:3px}
.nav{left:344px;top:127px;display:flex;gap:23px;font-size:12px;color:var(--muted);white-space:nowrap}
.hero-title{left:25px;top:298px;font-size:56px;line-height:64px;font-weight:700;width:560px}
.hero-copy{left:24px;top:438px;font-size:14px;line-height:24px;color:var(--muted);width:340px}
.hero-art{left:628px;top:212px;width:431px;height:494px;border-radius:18px;background:radial-gradient(circle at 40% 35%,#c873b0,#5a3390 45%,#1c1440 80%)}
.divider{left:1080px;top:100px;width:1px;height:959px;background:var(--line)}
.side-title{left:1144px;top:306px;font-size:42px;font-weight:700;white-space:nowrap}
.plan{left:1112px;top:515px;width:120px;height:75px;border-radius:10px;background:#221a63;padding:12px;font-size:9px;color:#c9c4ff;white-space:nowrap}
.plan b{display:block;font-size:13px;color:var(--orange);margin-bottom:6px}
.features{left:1122px;top:608px;list-style:none;font-size:9px;color:var(--muted);white-space:nowrap}
.features li{height:25px;display:flex;gap:8px}
.features li::before{content:"✓";color:#3ccf6e}
.features li.off::before{color:transparent}
.update-title{left:92px;top:752px;font-size:31px;line-height:38px;font-weight:700}
.update-copy{left:92px;top:834px;font-size:12px;line-height:18px;color:var(--muted);width:350px}
.class-icon{width:100px;height:100px;border-radius:20px;background:#15131f}
.class-icon span{position:absolute;left:22px;top:22px;width:56px;height:56px;border-radius:50%}
.classes-title{left:0;width:1043px;top:1000px;text-align:center;font-size:37px;font-weight:700;white-space:nowrap}
.veil{inset:0;background:var(--veil)}
.age-gate{left:320px;top:330px;width:560px;height:390px}
.age-gate svg{position:absolute;inset:0}
.gate-brand{position:absolute;left:0;right:0;top:100px;display:flex;align-items:center;justify-content:center;gap:10px;font-family:"Inter",sans-serif;font-size:24px;font-weight:600;color:#fff;white-space:nowrap}
.gate-brand i{width:14px;height:14px;background:#fff}
.gate-question{position:absolute;left:0;right:0;top:195px;text-align:center;font-family:"Inter",sans-serif;font-size:17px;color:var(--modal-ink)}
.gate-actions{position:absolute;left:159px;top:245px;display:flex;gap:17px}
.gate-actions a{width:115px;height:38px;background:var(--btn);color:#fff;font-family:"Inter",sans-serif;font-size:17px;display:flex;align-items:center;justify-content:center;text-decoration:none}
.gate-remember{position:absolute;left:227px;top:316px;display:flex;align-items:center;gap:9px;font-family:"Inter",sans-serif;font-size:13px;color:var(--modal-ink);white-space:nowrap}
.gate-remember i{width:10px;height:10px;background:var(--modal-ink)}
</style>
</head>
<body>
<div class="abs top-band"></div>
<div class="abs promo-title">with your custom cards</div>
<div class="abs btn btn-solid" style="left:945px;top:46px;width:128px;height:40px">VIEW ALL CARDS</div>
<div class="abs btn btn-ghost" style="left:1086px;top:46px;width:140px;height:40px">SEE DECK BUILDER</div>

<div class="abs brand"><span class="brand-mark"></span>Mythbound</div>
<nav class="abs nav"><span>Overview</span><span>Features</span><span>Getting Started</span><span>Meida</span><span>FAQ</span></nav>
<div class="abs btn btn-ghost" style="left:870px;top:116px;width:67px;height:29px;font-size:8px">ACCOUNT</div>
<div class="abs btn" style="left:945px;top:116px;width:72px;height:29px;font-size:8px;background:var(--orange);color:#3a2300">SUBSCRIBE</div>

<h1 class="abs hero-title">Beautiful game, intense realism</h1>
<p class="abs hero-copy">Welcome to Mythbound, the strategy card game that's easy to learn but impossible to put down.</p>
<div class="abs btn btn-solid" style="left:24px;top:505px;width:94px;height:37px">PLAY NOW</div>
<div class="abs btn btn-ghost" style="left:129px;top:505px;width:95px;height:37px">LEARN MORE</div>
<div class="abs hero-art" role="img" aria-label="Illustrated hero cards with fantasy characters"></div>

<div class="abs divider"></div>
<div class="abs side-title">Discover</div>
<div class="abs plan"><b>Essential</b>1 Month - $14.99<br>Billed every 1 month</div>
<ul class="abs features">
  <li>Rating Matches</li><li>Exclusive Badges</li><li>Extra Crystals</li><li>Game Help</li><li>Deck Sharing</li>
  <li class="off">Deck Builder</li><li class="off">Deck Building</li><li class="off">New Hero Trials</li><li class="off">Monthly Cards</li>
</ul>

<h2 class="abs update-title">Synergy of the light<br>update is now live</h2>
<p class="abs update-copy">Combine new spells and character abilities however you want. Create your own classes and share your decks.</p>
<div class="abs btn btn-solid" style="left:92px;top:887px;width:94px;height:36px">BUY NOW</div>
<div class="abs btn btn-ghost" style="left:198px;top:887px;width:94px;height:36px">LEARN MORE</div>

<div class="abs class-icon" style="left:515px;top:791px" role="img" aria-label="Shadow class emblem"><span style="background:radial-gradient(#a23ad6,#3b1060)"></span></div>
<div class="abs class-icon" style="left:625px;top:763px" role="img" aria-label="Nature class emblem"><span style="background:radial-gradient(#3fd68a,#0f4a2c)"></span></div>
<div class="abs class-icon" style="left:734px;top:805px" role="img" aria-label="Fire class emblem"><span style="background:radial-gradient(#ffb13c,#7a3a06)"></span></div>
<div class="abs class-icon" style="left:847px;top:773px" role="img" aria-label="Frost class emblem"><span style="background:radial-gradient(#4aa3ff,#113a73)"></span></div>

<h2 class="abs classes-title">Master 4 base hero classes</h2>

<div class="abs veil"></div>

<section class="abs age-gate" aria-label="Age verification">
  <svg viewBox="0 0 560 390" fill="none" stroke="var(--modal-edge)" stroke-width="3">
    <rect x="19" y="25" width="522" height="350" fill="var(--modal)" stroke-width="6"/>
    <path d="M63 25V16H497V25M63 375V384H497V375M19 70H10V330H19M541 70H550V330H541"/>
  </svg>
  <div class="gate-brand"><i></i>Velvet Dice Night</div>
  <p class="gate-question">Are you over 18 years of age?</p>
  <div class="gate-actions"><a href="#">Yes</a><a href="#">No</a></div>
  <label class="gate-remember"><i></i>Remember me</label>
</section>
</body>
</html>
```